Design a modern, classy & professional business card for an online real estate agency, specializing in medium-luxury properties in Thailand and later in Singapore and UK.

Possible design ideas so far: (not essential)

- curved corner(s) to the card, white on front & turquoise on back or visa versa.

- front of card - clear and simple, company name in metallic grey/monochrome, logo graphic & company name on front in spot UV or embossed/debossed effect.

- back of card - large, close-cropped, 'ghost' patterns of the C-shaped curves of logo, or company name repeated on back of card in spot UV.

Target Market(s)

- young to middle-aged professionals mainly (but ideally should design should suit all)

- UK, US,EU,AUS & ASIAN mainly (but ideally should design should suit all countries)

Industry/Entity Type

Real Estate

Requirements
Must have
• THEME:
- Luxurious & Modern
- Clean & striking
- Unique & creative

INFO:
- Logo & company name on front
- Contact details on back:

Tobias Hennlund
Managing Director

www.velmontestates.asia
www.velmontestates.co.uk

Tel: 083-274-6159
email: tobias@velmontestates.asia

(contact details can be displayed in any order as suites design.)

Nice to have
• - curved corner(s) to the card, white on front & turquoise on back or visa versa.

Should not have
• - No generic images of properties, palm trees/coconut trees etc.

- No other other bold colors, except for main turquoise, grey, metallic white & black theme.

- No obvious business card templates

```html
<!DOCTYPE html>
<html lang="en">
<head>
<meta charset="utf-8">
<title>Velmont Estates – Business Card</title>
<link rel="stylesheet" href="https://fonts.googleapis.com/css2?family=Cormorant+Garamond:wght@500&family=Open+Sans:wght@400;600&display=swap">
<style>
  :root {
    --stage: #b3b7be;
    --card-white: #f4f4f4;
    --card-shade: #e2e3e4;
    --turquoise: #14c6c3;
    --grey-mark: #7d7d7d;
    --grey-band: #808080;
    --ink: #1f2b2b;
  }
  * { margin: 0; padding: 0; box-sizing: border-box; }
  html, body { width: 1200px; height: 866px; overflow: hidden; }
  body {
    background: var(--stage);
    position: relative;
    font-family: "Open Sans", sans-serif;
  }
  .card {
    position: absolute;
    top: 278px;
    width: 540px;
    height: 310px;
    overflow: hidden;
    background: radial-gradient(ellipse at 45% 45%, #ffffff 0%, var(--card-white) 55%, var(--card-shade) 100%);
  }
  .card--front { left: 45px; }
  .card--back { left: 615px; }

  .brand {
    position: absolute;
    display: flex;
    align-items: center;
    gap: 12px;
  }
  .brand__square {
    width: 58px;
    height: 58px;
    background: var(--turquoise);
    flex: none;
  }
  .brand__name {
    font-family: "Cormorant Garamond", serif;
    font-weight: 500;
    color: var(--grey-mark);
    line-height: 1;
  }
  .brand__word { display: block; font-size: 54px; letter-spacing: -0.5px; }
  .brand__sub { display: block; font-size: 16px; letter-spacing: 5px; margin-top: 2px; }
  .card--front .brand { left: 140px; top: 112px; }

  .back-art { position: absolute; inset: 0; }
  .card--back .brand {
    left: 42px; top: 98px;
    flex-direction: column;
    align-items: flex-start;
    gap: 10px;
  }
  .card--back .brand__square { width: 50px; height: 50px; margin-left: 20px; }
  .card--back .brand__word { font-size: 46px; }
  .card--back .brand__sub { font-size: 14px; letter-spacing: 4.5px; }

  .contact {
    position: absolute;
    right: 26px;
    top: 24px;
    text-align: right;
    color: var(--ink);
    font-size: 12.5px;
    line-height: 1.35;
  }
  .contact__name { font-weight: 600; font-size: 14px; }
  .contact__role { font-size: 14px; margin-bottom: 56px; }
  .contact__address { margin-bottom: 12px; }
  .contact__line { display: flex; justify-content: flex-end; align-items: center; gap: 5px; }
  .contact__line svg { width: 11px; height: 11px; fill: var(--ink); }
</style>
</head>
<body>

<section class="card card--front" aria-label="Card front">
  <div class="brand">
    <span class="brand__square"></span>
    <span class="brand__name">
      <span class="brand__word">Velmont</span>
      <span class="brand__sub">ESTATES</span>
    </span>
  </div>
</section>

<section class="card card--back" aria-label="Card back">
  <svg class="back-art" viewBox="0 0 540 310" preserveAspectRatio="none" aria-hidden="true">
    <rect width="540" height="310" fill="var(--turquoise)"/>
    <path d="M0,0 H175 C265,30 310,140 282,220 C270,255 255,285 238,310 H0 Z" fill="var(--card-white)"/>
    <path d="M300,120 C328,190 318,255 265,310 H285 C336,250 342,185 300,120 Z" fill="var(--grey-band)"/>
  </svg>

  <div class="brand">
    <span class="brand__square"></span>
    <span class="brand__name">
      <span class="brand__word">Velmont</span>
      <span class="brand__sub">ESTATES</span>
    </span>
  </div>

  <div class="contact">
    <p class="contact__name">Lena Orwick</p>
    <p class="contact__role">Consultant</p>
    <p class="contact__address">041,12th floor,Mall<br>Harbor Road LKG</p>
    <p class="contact__line">014 552 7310
      <svg viewBox="0 0 24 24"><path d="M6.6 10.8a15 15 0 0 0 6.6 6.6l2.2-2.2a1 1 0 0 1 1-.25 11.4 11.4 0 0 0 3.6.57 1 1 0 0 1 1 1V20a1 1 0 0 1-1 1A17 17 0 0 1 3 4a1 1 0 0 1 1-1h3.5a1 1 0 0 1 1 1c0 1.25.2 2.45.57 3.6a1 1 0 0 1-.25 1z"/></svg>
    </p>
    <p class="contact__line">014 552 7310
      <svg viewBox="0 0 24 24"><path d="M6 3h9v5H6zM4 9h16a2 2 0 0 1 2 2v7h-4v3H6v-3H2v-7a2 2 0 0 1 2-2zm4 7v3h8v-3z"/></svg>
    </p>
    <p class="contact__line">lena@velmont.asia
      <svg viewBox="0 0 24 24"><path d="M2 5h20v14H2zm2 2v.5l8 5 8-5V7z"/></svg>
    </p>
    <p class="contact__line">www.velmontestates.asia</p>
  </div>
</section>

</body>
</html>
```